Business card design

Hi,
I need to have a business card design based on the current logo.
If competitive I not put it out to everyone.

It can be single of double sided

Target Market(s)

Food businesses

Industry/Entity Type

Food Manufacturing

Contact Information for Business Card

Details will on card will be as follows Name = Marcus Bell Email = Marcus@PanHearth.com.au Phone = 0418563207 Address = 57 Larkin Street , Fortitude Valley QLD 4006 Australia

Font styles to use
Other font styles liked:
• based on two fonts - Adelle & Museo

Requirements
Must have
• Based on the on switch concept

```html
<!DOCTYPE html>
<html lang="en">
<head>
<meta charset="utf-8">
<title>PanHearth Business Card</title>
<link rel="stylesheet" href="https://fonts.googleapis.com/css2?family=Montserrat:wght@600;700&family=Arimo:wght@400&family=Roboto+Slab:wght@500&display=swap">
<style>
  :root {
    --bg: #1d1d1d;
    --card: #0b0b0b;
    --red: #ec2a4b;
    --white: #f4f4f4;
    --grey: #c9c9c9;
    --rule: #3a3a3a;
  }
  * { box-sizing: border-box; margin: 0; padding: 0; }
  html, body { width: 1200px; height: 900px; overflow: hidden; }
  body {
    background: radial-gradient(ellipse at 50% 40%, #2a2a2a 0%, var(--bg) 70%);
    position: relative;
  }
  .card {
    position: absolute;
    top: 285px;
    width: 540px;
    height: 330px;
    background: var(--card);
    box-shadow: 0 14px 30px rgba(0,0,0,.6);
  }
  .card--front { left: 40px; }
  .card--back { left: 620px; }

  .brand {
    position: absolute;
    display: flex;
    align-items: center;
    gap: 10px;
  }
  .brand__dot {
    width: 26px; height: 26px;
    border-radius: 50%;
    background: var(--red);
    flex: none;
  }
  .brand__name {
    font-family: 'Montserrat', sans-serif;
    font-weight: 600;
    color: var(--white);
    letter-spacing: 1px;
    white-space: nowrap;
  }
  .card--front .brand { left: 34px; top: 148px; }
  .card--front .brand__name { font-size: 27px; }

  .divider {
    position: absolute;
    left: 268px; top: 92px;
    width: 1px; height: 160px;
    background: var(--rule);
  }
  .details {
    position: absolute;
    left: 292px; top: 96px;
    font-family: 'Arimo', sans-serif;
    color: var(--grey);
  }
  .details__name {
    font-family: 'Montserrat', sans-serif;
    font-weight: 700;
    color: var(--red);
    font-size: 18px;
    letter-spacing: .5px;
    margin-bottom: 8px;
  }
  .details__address { font-size: 13px; line-height: 17px; margin-bottom: 16px; }
  .contact { list-style: none; font-size: 13px; color: var(--white); }
  .contact li { display: flex; align-items: center; gap: 8px; line-height: 19px; white-space: nowrap; }
  .contact svg { width: 12px; height: 12px; flex: none; }
  .contact .accent { color: var(--red); }

  .card--back .brand { left: 150px; top: 132px; gap: 12px; }
  .card--back .brand__dot { width: 34px; height: 34px; }
  .card--back .brand__name { font-size: 36px; }
  .tagline {
    position: absolute;
    left: 198px; top: 180px;
    font-family: 'Roboto Slab', serif;
    font-weight: 500;
    font-size: 13px;
    color: var(--white);
    white-space: nowrap;
  }
</style>
</head>
<body>
  <section class="card card--front">
    <div class="brand">
      <span class="brand__dot"></span>
      <span class="brand__name">PANHEARTH</span>
    </div>
    <div class="divider"></div>
    <div class="details">
      <h1 class="details__name">MARCUS BELL</h1>
      <p class="details__address">57 Larkin Street<br>Marlow Heights<br>QLD 4187 Australia</p>
      <ul class="contact">
        <li>
          <svg viewBox="0 0 24 24" aria-hidden="true"><path fill="#ec2a4b" d="M6.6 10.8a15 15 0 0 0 6.6 6.6l2.2-2.2c.3-.3.7-.4 1-.2 1.1.4 2.3.6 3.6.6.6 0 1 .4 1 1V20c0 .6-.4 1-1 1A17 17 0 0 1 3 4c0-.6.4-1 1-1h3.5c.6 0 1 .4 1 1 0 1.3.2 2.5.6 3.6.1.3 0 .7-.2 1z"/></svg>
          0418563207
        </li>
        <li>
          <svg viewBox="0 0 24 24" aria-hidden="true"><rect x="2" y="5" width="20" height="14" fill="#ec2a4b"/><path d="M2 5l10 8 10-8" fill="none" stroke="#0b0b0b" stroke-width="2"/></svg>
          Marcus@PanHearth.com.au
        </li>
        <li>
          <svg viewBox="0 0 24 24" aria-hidden="true"><g fill="none" stroke="#ec2a4b" stroke-width="2"><circle cx="12" cy="12" r="10"/><ellipse cx="12" cy="12" rx="4" ry="10"/><path d="M2 12h20"/></g></svg>
          <span>www.<span class="accent">PanHearth</span>.com.au</span>
        </li>
      </ul>
    </div>
  </section>

  <section class="card card--back">
    <div class="brand">
      <span class="brand__dot"></span>
      <span class="brand__name">PANHEARTH</span>
    </div>
    <p class="tagline">Kitchen Supply Made Simple</p>
  </section>
</body>
</html>
```